School Poster

Design so that these can be placed in classrooms across the school.

Attached is another design we have had done. Use a similar theme.

Consider using themes from https://corvalhs.edq.example.au/

please edit Binder1 doc.

Students and teachers

```html
<!DOCTYPE html>
<html lang="en">
<head>
<meta charset="utf-8">
<title>Corval State High School – Classroom Posters</title>
<link href="https://fonts.googleapis.com/css2?family=Archivo+Black&family=Archivo:ital,wght@0,600;0,700;0,800;1,700&family=Arimo:ital,wght@0,400;0,700;1,400&display=swap" rel="stylesheet">
<style>
  :root{
    --stage:#b3b3b3;
    --navy:#253a7a;
    --royal:#1f4597;
    --yellow:#f1e459;
    --gold:#fbd65a;
    --lav:#e4e3f3;
    --lav-dark:#c8c7e5;
    --cream:#faf6d6;
    --cream-dark:#f5eeb8;
    --ink:#1d1d2b;
    --white:#ffffff;
  }
  *{box-sizing:border-box;margin:0;padding:0}
  html,body{width:1200px;height:1200px;overflow:hidden}
  body{background:var(--stage);position:relative;font-family:"Arimo",Arial,sans-serif;color:var(--ink)}
  .poster{position:absolute;top:240px;width:511px;height:720px;background:var(--white);overflow:hidden}
  .poster--steps{left:74px}
  .poster--ai{left:621px}
  .header-art{position:absolute;left:0;top:0}
  .crest{position:absolute;width:90px;height:90px;border-radius:50%;background:var(--white);display:flex;align-items:center;justify-content:center;text-align:center;font-family:"Archivo",sans-serif;font-weight:800;font-size:15px;line-height:1.05;color:var(--navy)}
  .poster--steps .crest{left:30px;top:20px}
  .poster--ai .crest{left:28px;top:18px}
  .eyebrow{position:absolute;font-family:"Archivo",sans-serif;font-weight:700;color:var(--white);white-space:nowrap}
  .headline{position:absolute;font-family:"Archivo Black",sans-serif;color:var(--yellow);white-space:nowrap}
  .poster--steps .eyebrow{left:136px;top:14px;font-size:18.5px;letter-spacing:.2px}
  .poster--steps .headline{left:134px;top:38px;font-size:41.5px;line-height:41px}
  .poster--ai .eyebrow{left:134px;top:30px;font-size:23.5px}
  .poster--ai .headline{left:134px;top:59px;font-size:44px;line-height:50px}

  /* step cards */
  .step{position:absolute;left:25px;width:461px}
  .step__tab{position:absolute;left:0;top:0;height:20px;padding:0 10px 0 28px;border:1.5px solid var(--navy);border-radius:0 12px 12px 0;font-family:"Archivo",sans-serif;font-weight:800;font-size:15px;line-height:17px;color:var(--navy);white-space:nowrap;z-index:2}
  .step__num{position:absolute;left:-1px;top:-1px;width:21px;height:20px;border:1.5px solid var(--navy);border-radius:0 10px 10px 0;background:var(--white);text-align:center;font-size:13px;line-height:17px}
  .step__box{position:absolute;left:0;right:0;border:1.5px solid var(--navy);border-radius:0 6px 6px 6px;overflow:hidden;display:flex}
  .step__side{width:155px;flex:none;display:flex;flex-direction:column;align-items:center;justify-content:center;text-align:center;font-family:"Archivo",sans-serif;font-style:italic;font-weight:700;font-size:14px;line-height:16.5px;border-right:2px dotted var(--navy)}
  .step__side svg{margin-bottom:8px}
  .step__list{flex:1;list-style:none;padding-top:15px}
  .step__list li{height:22px;line-height:22px;font-size:14px;padding-left:26px;position:relative;white-space:nowrap}
  .step__list li::before{content:"";position:absolute;left:15px;top:9px;width:4.5px;height:4.5px;border-radius:50%;background:var(--royal)}
  .step__note{font-style:italic;font-size:14px;padding:19px 0 0 15px}

  .step--think{top:162px}
  .step--think .step__tab{background:var(--gold)}
  .step--think .step__box{top:10px;height:107px}
  .step--think .step__side,.step--ask .step__side{background:var(--gold);color:var(--royal)}
  .step--think .step__list,.step--ask .step__list{background:var(--lav)}
  .step--think .step__list li:nth-child(odd),.step--ask .step__list li:nth-child(odd){background:var(--lav-dark)}

  .step--check{top:311px}
  .step--check .step__tab{background:var(--royal);color:var(--white);border-color:var(--gold)}
  .step--check .step__num{background:var(--white);color:var(--royal);border-color:var(--gold)}
  .step--check .step__box{top:9px;height:155px;border-color:var(--gold)}
  .step--check .step__side{background:var(--royal);color:var(--white)}
  .step--check .step__list{background:var(--cream);padding-top:8px}
  .step--check .step__list li:nth-child(odd){background:var(--cream-dark)}

  .step--ask{top:507px}
  .step--ask .step__tab{background:var(--gold)}
  .step--ask .step__box{top:10px;height:128px}
  .step--ask .step__list{padding-top:16px}

  /* footer */
  .footer-band{position:absolute;left:0;right:0;top:685px;height:20px;background:var(--navy)}
  .motto{position:absolute;top:682px;height:26px;border-radius:13px;background:var(--yellow);border:1.5px solid var(--white);font-family:"Archivo",sans-serif;font-weight:800;color:var(--royal);text-align:center;white-space:nowrap}
  .poster--steps .motto{left:89px;width:331px;font-size:12.5px;line-height:23px;letter-spacing:1.6px;padding-left:1.6px}
  .poster--ai .motto{left:25px;width:462px;font-size:10.5px;line-height:23px;letter-spacing:.3px}

  /* AI rule blocks */
  .rule{position:absolute;left:0;width:511px}
  .rule__panel{position:absolute;left:104px;width:390px;top:0;bottom:0;background:var(--cream);border:1.5px solid var(--navy);border-radius:7px}
  .rule__label{position:absolute;left:14px;width:178px;background:var(--navy);border-radius:7px;color:var(--white);font-family:"Archivo",sans-serif;font-weight:700;font-size:13px;line-height:16px;text-align:center;display:flex;align-items:flex-end;justify-content:center;padding-bottom:10px}
  .rule__badge{position:absolute;left:80px;width:44px;height:44px}
  .rule__list{position:absolute;left:205px;width:273px;top:6px;bottom:8px;list-style:none;border-left:2px dotted var(--gold);display:flex;flex-direction:column}
  .rule__list li{flex:1;display:flex;align-items:center;padding-left:23px;position:relative;font-size:13.5px;line-height:16.5px;border-bottom:1px solid var(--gold)}
  .rule__list li:last-child{border-bottom:none}
  .rule__list li::before{content:"";position:absolute;left:10px;top:50%;margin-top:-2.5px;width:5px;height:5px;border-radius:50%;background:var(--royal)}

  .rule--must{top:151px;height:158px}
  .rule--must .rule__label{top:61px;height:55px}
  .rule--must .rule__badge{top:38px}
  .rule--help{top:322px;height:157px}
  .rule--help .rule__label{top:46px;height:85px}
  .rule--help .rule__badge{top:24px}
  .rule--cannot{top:493px;height:174px}
  .rule--cannot .rule__label{top:71px;height:56px}
  .rule--cannot .rule__badge{top:49px}
</style>
</head>
<body>

<section class="poster poster--steps" aria-label="Before you ask the teacher poster">
  <svg class="header-art" width="511" height="160" viewBox="0 0 511 160" aria-hidden="true">
    <path d="M0 0H511V150Q330 105 0 138Z" fill="var(--navy)"/>
    <path d="M0 138Q150 120 300 123Q140 126 0 150Z" fill="var(--yellow)"/>
  </svg>
  <div class="crest">CORVAL<br>SHS</div>
  <p class="eyebrow">BEFORE YOU ASK THE TEACHER.....</p>
  <h1 class="headline">TRY THESE<br>STEPS FIRST!</h1>

  <div class="step step--think">
    <div class="step__tab"><span class="step__num">1</span>THINK FIRST</div>
    <div class="step__box">
      <div class="step__side">
        <svg width="36" height="36" viewBox="0 0 36 36" fill="none" stroke="var(--royal)" stroke-width="1.6" aria-hidden="true">
          <path d="M9 33v-7c-4-3-6-7-5-12 2-7 9-11 16-9 6 2 9 7 8 13l3 5h-3v4c0 2-2 3-4 3h-3v3"/>
          <circle cx="19" cy="14" r="4"/><circle cx="19" cy="14" r="7" stroke-dasharray="2.5 2"/>
        </svg>
        Don’t give up<br>straight away
      </div>
      <ul class="step__list">
        <li>Read the question carefully</li>
        <li>Identify what you already know</li>
        <li>Try a strategy you’ve used before</li>
        <li>Give yourself thinking time</li>
      </ul>
    </div>
  </div>

  <div class="step step--check">
    <div class="step__tab"><span class="step__num">2</span>CHECK YOUR SUPPORTS</div>
    <div class="step__box">
      <div class="step__side">
        <svg width="34" height="34" viewBox="0 0 34 34" fill="none" stroke="var(--white)" stroke-width="1.6" aria-hidden="true">
          <path d="M10 4h12l7 7v20H10V22"/><path d="M22 4v7h7"/><path d="M15 16h10M17 21h8M17 26h8"/>
          <circle cx="9" cy="24" r="6"/><path d="M6 24l2 2 4-4"/>
        </svg>
        Before asking<br>for help, check:
      </div>
      <ul class="step__list">
        <li>Learning goal and success criteria</li>
        <li>Worked examples</li>
        <li>Class notes</li>
        <li>Classroom displays</li>
        <li>StudyHub resources</li>
        <li>Task sheet and instructions</li>
      </ul>
    </div>
  </div>

  <div class="step step--ask">
    <div class="step__tab"><span class="step__num">3</span>ASK 3 BEFORE ME</div>
    <div class="step__box">
      <div class="step__side">
        <svg width="38" height="32" viewBox="0 0 38 32" fill="none" stroke="var(--royal)" stroke-width="1.6" aria-hidden="true">
          <path d="M2 2h18v13H9l-4 4v-4H2z"/><path d="M9 6q2-2 4 0t-2 4v1"/>
          <path d="M16 13h20v14h-3v4l-4-4H16z"/><path d="M20 18h12M20 22h12"/>
        </svg>
        Ask three sources<br>before asking the<br>teacher:
      </div>
      <div class="step__body" style="flex:1;background:var(--lav)">
        <ul class="step__list">
          <li>A person (partner or neighbour)</li>
          <li>A place (notes, display, StudyHub)</li>
          <li>A resource (worked example, task sheet)</li>
        </ul>
        <p class="step__note">Then ask the teacher if you still need help</p>
      </div>
    </div>
  </div>

  <div class="footer-band"></div>
  <p class="motto">WE BELIEVE. WE STRIVE. WE ACHIEVE</p>
</section>

<section class="poster poster--ai" aria-label="Using AI responsibly poster">
  <svg class="header-art" width="511" height="132" viewBox="0 0 511 132" aria-hidden="true">
    <path d="M0 0H66V131H0Z" fill="var(--yellow)"/>
    <path d="M0 131H50Q66 131 74 120L66 131Z" fill="var(--yellow)"/>
    <path d="M66 0H511V131H95Q70 131 66 110Z" fill="var(--navy)"/>
  </svg>
  <div class="crest">CORVAL<br>SHS</div>
  <p class="eyebrow">USING AI AND OTHER TOOLS</p>
  <h1 class="headline">RESPONSIBLY</h1>

  <div class="rule rule--must">
    <div class="rule__panel"></div>
    <div class="rule__label">WHAT YOU MUST DO</div>
    <svg class="rule__badge" viewBox="0 0 44 44" aria-hidden="true"><circle cx="22" cy="22" r="21" fill="var(--gold)" stroke="var(--white)" stroke-width="1.5"/><path d="M11 22l8 8 14-15" fill="none" stroke="var(--royal)" stroke-width="5" stroke-linecap="round" stroke-linejoin="round"/></svg>
    <ul class="rule__list">
      <li>Complete your own work</li>
      <li>Demonstrate your progress (drafts, notes, planning, revisions)</li>
      <li>Use feedback to improve your work</li>
      <li>Demonstrate your understanding of the ideas in your submission</li>
    </ul>
  </div>

  <div class="rule rule--help">
    <div class="rule__panel"></div>
    <div class="rule__label">WHAT AI CAN HELP YOU<br>DO (WHEN APPROVED<br>BY YOUR TEACHER)</div>
    <svg class="rule__badge" viewBox="0 0 44 44" aria-hidden="true"><circle cx="22" cy="22" r="21" fill="var(--gold)" stroke="var(--white)" stroke-width="1.5"/><path d="M11 22l8 8 14-15" fill="none" stroke="var(--royal)" stroke-width="5" stroke-linecap="round" stroke-linejoin="round"/></svg>
    <ul class="rule__list">
      <li>Brainstorm ideas</li>
      <li>Check spelling, grammar and clarity</li>
      <li>Read your work aloud using<br>text-to-speech tools</li>
      <li>Help identify areas for improvement in a draft</li>
    </ul>
  </div>

  <div class="rule rule--cannot">
    <div class="rule__panel"></div>
    <div class="rule__label">WHAT YOU CANNOT DO</div>
    <svg class="rule__badge" viewBox="0 0 44 44" aria-hidden="true"><circle cx="22" cy="22" r="21" fill="var(--gold)" stroke="var(--white)" stroke-width="1.5"/><path d="M13 13l18 18M31 13L13 31" fill="none" stroke="var(--royal)" stroke-width="5" stroke-linecap="round"/></svg>
    <ul class="rule__list">
      <li>Submit AI generated work as your own</li>
      <li>Copy and paste AI responses without acknowledging or adapting them</li>
      <li>Use AI tools to complete the whole task for you</li>
      <li>Submit work that does not demonstrate your understanding</li>
    </ul>
  </div>

  <div class="footer-band"></div>
  <p class="motto">IF YOU DIDN’T CREATE, DEVELOP AND UNDERSTAND IT, IT ISN’T YOUR WORK.</p>
</section>

</body>
</html>
```